Window and GutterCleaning Flyer A5 size double sided.

We need a double sided A5 flyer. Side 1, is for window cleaning, side 2 is for gutter cleaning. Licensed by Borough of Marlow Council.
Phone number 0800 473 1926.
Business address 17 Fallowmere Close, North Brack Edinburgh EH31 4LP.
www.clearpane-hub-services.com
We use a LoftEye Gutter inspection Cam to view your gutters first to see if they need doing.
Window cleaning ; Professional window cleaning services, what we offer, water fed pole window cleaning able to reach windows up to 60 feet.
Conservatory cleaning.
Conservatory roof cleaning.
Fascias & Soffits cleaning.
Excellent Customer Service.
Target Market(s)
domestic houses
Industry/Entity Type
window cleaning
Look and feel
Each slider illustrates characteristics of the customer's brand and the style your logo design should communicate.

```html
<!DOCTYPE html>
<html lang="en">
<head>
<meta charset="utf-8">
<title>ClearPane Hub – Window &amp; Gutter Cleaning Flyer</title>
<link rel="stylesheet" href="https://fonts.googleapis.com/css2?family=Arimo:wght@400;700&family=Roboto+Condensed:wght@400&display=swap">
<style>
  :root {
    --navy: #2d2a5e;
    --sky: #a6cbee;
    --ink: #1a1a1a;
    --paper: #ffffff;
    --backdrop: #e9e7e3;
  }
  * { box-sizing: border-box; margin: 0; padding: 0; }
  html, body { width: 1200px; height: 928px; overflow: hidden; }
  body { background: var(--backdrop); font-family: "Arimo", Arial, sans-serif; color: var(--ink); position: relative; }
  .spread { position: absolute; left: 28px; top: 70px; width: 1240px; height: 875px; transform: scale(0.9); transform-origin: 0 0; }
  .flyer { position: absolute; top: 0; width: 620px; height: 875px; background: var(--paper); overflow: hidden; box-shadow: 0 2px 8px rgba(0,0,0,.25); }
  .flyer--windows { left: 0; }
  .flyer--gutters { left: 636px; }
  .flyer__frame { position: absolute; inset: 0; }
  .abs { position: absolute; }
  .licence { right: 22px; top: 14px; text-align: right; color: var(--sky); font-weight: 700; font-size: 15px; line-height: 24px; white-space: nowrap; }
  .brand { left: 18px; top: 150px; display: flex; align-items: center; gap: 8px; color: var(--navy); font-weight: 700; font-size: 24px; white-space: nowrap; }
  .brand__mark { width: 18px; height: 18px; background: var(--navy); }
  .headline { left: 16px; font-size: 22px; color: var(--ink); white-space: nowrap; }
  .lede { left: 16px; font-size: 16px; line-height: 26px; color: var(--ink); white-space: nowrap; }
  .photo { position: absolute; }
  .contact-label { font-size: 11.5px; color: var(--navy); white-space: nowrap; }
  .phone { display: flex; align-items: center; gap: 12px; font-family: "Roboto Condensed", "Arial Narrow", sans-serif; font-size: 37px; color: var(--navy); white-space: nowrap; }
  .address, .email { left: 24px; font-size: 12px; color: var(--navy); line-height: 16px; display: flex; gap: 10px; align-items: flex-start; }
  .web { left: 20px; top: 845px; font-size: 12px; color: #fff; display: flex; gap: 8px; align-items: center; }
  .caption { text-align: center; font-size: 16px; line-height: 21px; color: var(--navy); width: 196px; }
  .inspect { left: 10px; top: 588px; font-size: 22px; line-height: 34.5px; color: var(--ink); width: 205px; }
</style>
</head>
<body>
<div class="spread">

  <section class="flyer flyer--windows">
    <svg class="flyer__frame" width="620" height="875" viewBox="0 0 620 875" aria-hidden="true">
      <rect width="620" height="360" fill="var(--navy)"/>
      <path d="M0,0 C330,0 575,95 620,285 L620,875 L0,875 Z" fill="var(--sky)"/>
      <path d="M0,6 C330,6 560,110 620,305 L620,875 L0,875 Z" fill="var(--paper)"/>
      <path d="M0,815 C180,798 420,812 620,812 L620,875 L0,875 Z" fill="var(--navy)"/>
      <path d="M360,842 C430,838 480,836 560,835" stroke="#fff" stroke-width="2" fill="none" opacity=".6"/>
    </svg>
    <div class="abs licence">Licensed by<br>Borough of Marlow Council</div>
    <div class="abs brand"><span class="brand__mark"></span>ClearPane Hub</div>
    <h1 class="abs headline" style="top:230px;font-weight:400">Professional Window Cleaning Services.</h1>
    <p class="abs lede" style="top:266px">What We Offer, Water Fed Pole, Window Cleaning Able To Reach<br>Windows Up To 60 Feet.</p>
    <div class="photo" style="left:0;top:335px;width:185px;height:373px;background:linear-gradient(160deg,#9cb8dc,#4f78b0 55%,#c6d6ea)" role="img" aria-label="Brush on a water fed pole spraying a window"></div>
    <div class="photo" style="left:191px;top:335px;width:151px;height:373px;background:linear-gradient(180deg,#9a5a45,#b5705a 50%,#8a6a4c)" role="img" aria-label="Brick house front with white windows and door"></div>
    <div class="photo" style="left:350px;top:335px;width:270px;height:373px;background:linear-gradient(135deg,#dfe3e6,#6f7a80 45%,#c9d0d4)" role="img" aria-label="Water fed pole cleaning a white framed window"></div>
    <div class="abs address" style="top:731px">
      <svg width="14" height="20" viewBox="0 0 14 20" aria-hidden="true"><path d="M7,0 C3,0 0,3 0,7 C0,12 7,20 7,20 C7,20 14,12 14,7 C14,3 11,0 7,0 Z" fill="var(--navy)"/><circle cx="7" cy="7" r="2.6" fill="#fff"/></svg>
      <span>17 Fallowmere Close, North Brack<br>Edinburgh EH31 4LP</span>
    </div>
    <div class="abs email" style="top:775px;align-items:center">
      <svg width="16" height="12" viewBox="0 0 16 12" aria-hidden="true"><rect width="16" height="12" fill="var(--navy)"/><path d="M0,0 L8,7 L16,0" stroke="#fff" stroke-width="1.4" fill="none"/></svg>
      <span>info@clearpane-hub-services.com</span>
    </div>
    <div class="abs contact-label" style="right:28px;top:736px">For More Information Contact Us</div>
    <div class="abs phone" style="right:22px;top:750px">
      <svg width="40" height="40" viewBox="0 0 40 40" aria-hidden="true"><circle cx="20" cy="20" r="18" fill="none" stroke="var(--navy)" stroke-width="2"/><path d="M14,11 C12,13 11,18 14,24 C17,30 21,32 24,31 L26,27 L22,24 L20,26 C18,24 16,20 16,18 L18,16 L17,11 Z" fill="var(--navy)"/></svg>
      <span>0800 473 1926</span>
    </div>
    <div class="abs web">
      <svg width="16" height="16" viewBox="0 0 16 16" aria-hidden="true"><g fill="none" stroke="#fff" stroke-width="1.2"><circle cx="8" cy="8" r="7"/><ellipse cx="8" cy="8" rx="3" ry="7"/><path d="M1,8 H15 M2.5,4.5 H13.5 M2.5,11.5 H13.5"/></g></svg>
      <span>www.clearpane-hub-services.com</span>
    </div>
  </section>

  <section class="flyer flyer--gutters">
    <svg class="flyer__frame" width="620" height="875" viewBox="0 0 620 875" aria-hidden="true">
      <rect width="620" height="360" fill="var(--navy)"/>
      <path d="M0,0 C330,0 575,95 620,285 L620,875 L0,875 Z" fill="var(--sky)"/>
      <path d="M0,6 C330,6 560,110 620,305 L620,875 L0,875 Z" fill="var(--paper)"/>
      <path d="M0,815 C180,798 420,812 620,812 L620,875 L0,875 Z" fill="var(--navy)"/>
      <path d="M360,842 C430,838 480,836 560,835" stroke="#fff" stroke-width="2" fill="none" opacity=".6"/>
    </svg>
    <div class="abs licence">Licensed by<br>Borough of Marlow Council</div>
    <div class="abs brand"><span class="brand__mark"></span>ClearPane Hub</div>
    <div class="abs contact-label" style="left:341px;top:158px">For More Information Contact Us</div>
    <div class="abs phone" style="left:254px;top:172px">
      <svg width="40" height="40" viewBox="0 0 40 40" aria-hidden="true"><circle cx="20" cy="20" r="18" fill="none" stroke="var(--navy)" stroke-width="2"/><path d="M14,11 C12,13 11,18 14,24 C17,30 21,32 24,31 L26,27 L22,24 L20,26 C18,24 16,20 16,18 L18,16 L17,11 Z" fill="var(--navy)"/></svg>
      <span>0800 473 1926</span>
    </div>
    <h2 class="abs headline" style="top:236px;font-weight:400">Gutters are an important part of your home.</h2>
    <p class="abs lede" style="top:272px">So why not set up an annual plan &amp; make sure you don’t run into<br>problems when winter comes.</p>
    <div class="photo" style="left:0;top:344px;width:196px;height:151px;background:linear-gradient(180deg,#cfe3f2,#f4f6f8 45%,#a8644c)" role="img" aria-label="White conservatory on a brick house"></div>
    <div class="photo" style="left:213px;top:344px;width:195px;height:151px;background:linear-gradient(160deg,#d9d4cf,#8f8a62 45%,#c8ccd2)" role="img" aria-label="Conservatory roof panels with moss"></div>
    <div class="photo" style="left:425px;top:344px;width:195px;height:151px;background:linear-gradient(200deg,#f2f2f2,#d4d7dc 50%,#9a5a46)" role="img" aria-label="House eaves showing gutter, fascia and soffit"></div>
    <div class="abs caption" style="left:0;top:500px">Conservatory<br>Cleaning</div>
    <div class="abs caption" style="left:213px;top:500px">Conservatory<br>Roof Cleaning</div>
    <div class="abs caption" style="left:425px;top:500px">Fascias And<br>Soffits Cleaning</div>
    <p class="abs inspect">We use a LoftEye Gutter inspection Cam to view your gutters first to see if they need doing.</p>
    <div class="photo" style="left:226px;top:580px;width:172px;height:112px;background:linear-gradient(160deg,#3a3a3a,#5a7a96 50%,#2a2a2a);border-radius:10px" role="img" aria-label="Handheld inspection camera screen"></div>
    <div class="photo" style="left:287px;top:677px;width:141px;height:121px;background:linear-gradient(180deg,#5e6a3e,#d8dadc 60%,#3c3a6a)" role="img" aria-label="Gutter filled with debris"></div>
    <div class="photo" style="left:428px;top:563px;width:192px;height:235px;background:linear-gradient(160deg,#7b8d52,#5f7a3e 50%,#8c9297)" role="img" aria-label="Vacuum pole clearing a roof gutter"></div>
    <div class="abs web">
      <svg width="16" height="16" viewBox="0 0 16 16" aria-hidden="true"><g fill="none" stroke="#fff" stroke-width="1.2"><circle cx="8" cy="8" r="7"/><ellipse cx="8" cy="8" rx="3" ry="7"/><path d="M1,8 H15 M2.5,4.5 H13.5 M2.5,11.5 H13.5"/></g></svg>
      <span>www.clearpane-hub-services.com</span>
    </div>
  </section>

</div>
</body>
</html>
```